HARBORLINE AUTO GLASS

Mobile Glass Shop:

1) Windshield REPAIR 2)Windshield replacment 3) Rear Windshield Replacment 4) Side Window Replacment 5) car window replacment 6) Power Window Repair.

Schedual a service within 24 hour with one of our certified technicians.
Updates

See "brightvane auto repair" web site for referance on the nature of our buisness and service. www.brightvane-example.com

Coding

```html
<!DOCTYPE html>
<html lang="en">
<head>
<meta charset="utf-8">
<title>Harborline Auto Glass</title>
<link rel="stylesheet" href="https://fonts.googleapis.com/css2?family=Bebas+Neue&family=Encode+Sans+Condensed:wght@400;600&display=swap">
<style>
  :root {
    --blue: #2a82bd;
    --blue-dark: #1f6ea6;
    --ink: #111418;
    --text: #3a3f45;
    --white: #ffffff;
    --bar: #3d4047;
  }
  * { margin: 0; padding: 0; box-sizing: border-box; }
  html, body { width: 1200px; height: 2180px; overflow: hidden; background: var(--white); }
  body { position: relative; font-family: "Encode Sans Condensed", sans-serif; color: var(--text); }
  .abs { position: absolute; }

  /* hero */
  .hero { left: 0; top: 0; width: 1200px; height: 683px; overflow: hidden;
    background: linear-gradient(100deg, #2f7fba 0%, #8ab8d8 22%, #e8f0f6 38%, #f3f4f5 55%, #d9d3cd 75%, #c9743a 100%); }
  .hero-photo { left: 380px; top: 80px; width: 820px; height: 603px;
    background: radial-gradient(ellipse at 70% 40%, rgba(40,90,160,.35), transparent 55%),
                radial-gradient(ellipse at 95% 80%, rgba(220,110,40,.55), transparent 55%);
    clip-path: polygon(28% 0, 100% 0, 100% 100%, 0 100%); }
  .logo-box { left: 144px; top: 0; width: 201px; height: 98px; background: var(--white);
    border-radius: 0 0 12px 12px; box-shadow: 0 3px 10px rgba(0,0,0,.15);
    display: flex; align-items: center; justify-content: center; gap: 8px; }
  .logo-mark { width: 12px; height: 12px; background: var(--blue); flex: none; }
  .logo-name { font-family: "Bebas Neue", sans-serif; color: var(--blue); font-size: 21px; line-height: 1; letter-spacing: .3px; white-space: nowrap; }
  .nav-band { left: 453px; top: 26px; width: 747px; height: 53px; background: var(--blue);
    clip-path: polygon(0 0, 100% 0, 100% 100%, 31px 100%); }
  .nav { left: 506px; top: 26px; height: 53px; display: flex; align-items: center; gap: 43px; }
  .nav a { color: var(--white); text-decoration: none; font-size: 16px; }
  .nav a.current { color: var(--ink); }
  .schedule { left: 852px; top: 13px; width: 203px; height: 78px; background: var(--white);
    border-radius: 4px; display: flex; align-items: center; gap: 8px; padding: 0 10px; }
  .schedule h3 { font-weight: 600; font-size: 18px; color: var(--blue); line-height: 1.1; white-space: nowrap; }
  .schedule p { font-size: 11px; color: var(--blue); line-height: 1.15; margin-top: 4px; }
  .welcome { left: 144px; top: 196px; font-family: "Bebas Neue", sans-serif; color: var(--ink); }
  .welcome .pre { font-size: 36px; line-height: 1; }
  .welcome .big { font-size: 108px; line-height: .88; }
  .welcome .sub { font-size: 66px; line-height: 1; letter-spacing: 7px; }
  .hero-text { left: 144px; top: 406px; width: 360px; font-size: 17px; line-height: 27px; color: #222; }
  .btn { display: flex; align-items: center; padding-left: 25px; width: 151px; height: 40px;
    background: var(--blue); color: var(--white); font-size: 17px; text-decoration: none;
    clip-path: polygon(0 0, 85% 0, 100% 100%, 0 100%); }

  /* services */
  .services { left: 144px; top: 628px; width: 912px; height: 688px; background: var(--white);
    border-radius: 12px; box-shadow: 0 0 12px rgba(0,0,0,.06); }
  .services h2 { position: absolute; top: 42px; width: 100%; text-align: center;
    font-family: "Bebas Neue", sans-serif; font-size: 46px; color: var(--blue); font-weight: 400; }
  .service { width: 236px; text-align: center; }
  .service svg { display: block; margin: 0 auto; }
  .service h4 { font-family: "Bebas Neue", sans-serif; font-weight: 400; font-size: 23px; color: var(--blue); margin-top: 18px; white-space: nowrap; }
  .service p { font-size: 15px; line-height: 27px; text-align: justify; margin: 10px 13px 0; }
  .service.active { background: var(--blue); border-radius: 12px; }
  .service.active h4, .service.active p { color: var(--white); }

  /* about */
  .about-photo { left: 0; top: 1387px; width: 525px; height: 344px;
    background: linear-gradient(120deg, #5b5f66, #b9bec4 45%, #d6533c 60%, #3a3d42);
    border-radius: 0 172px 172px 0 / 0 172px 172px 0; }
  .about { left: 568px; top: 1388px; width: 484px; }
  .about h2 { font-family: "Bebas Neue", sans-serif; font-weight: 400; font-size: 46px; color: var(--blue); line-height: 1.1; }
  .about p { font-size: 15.5px; line-height: 27.2px; text-align: justify; margin-top: 10px; color: #2a2e33; }
  .about .btn { margin-top: 20px; }

  /* footer */
  .footer { left: 0; top: 1826px; width: 1200px; height: 245px; background: var(--blue); }
  .foot-logo { left: 449px; top: 1811px; width: 305px; height: 151px; background: var(--white);
    border-radius: 14px; display: flex; align-items: center; justify-content: center; gap: 10px; }
  .foot-logo .logo-mark { width: 18px; height: 18px; }
  .foot-logo .logo-name { font-size: 30px; }
  .foot-text { left: 0; top: 1978px; width: 1200px; text-align: center; color: var(--white); font-size: 17px; }
  .foot-nav { left: 0; top: 2030px; width: 1200px; display: flex; justify-content: center; gap: 36px; }
  .foot-nav a { color: var(--white); text-decoration: none; font-size: 15px; }
  .bar { left: 0; top: 2071px; width: 1200px; height: 61px; background: var(--bar); color: var(--white);
    font-weight: 600; font-size: 15px; }
  .bar .item { position: absolute; top: 0; height: 61px; display: flex; align-items: center; gap: 8px; white-space: nowrap; }
  .dot { width: 14px; height: 14px; border-radius: 50%; background: var(--white); }
  .copy { left: 0; top: 2132px; width: 1200px; height: 48px; background: var(--blue); color: var(--white);
    font-size: 13px; font-weight: 600; display: flex; align-items: center; justify-content: center; }
</style>
</head>
<body>

<section class="abs hero" role="img" aria-label="Technician fitting a new windshield with a suction lifter"></section>
<div class="abs hero-photo" role="img" aria-label="Windshield installation photograph"></div>

<div class="abs logo-box"><span class="logo-mark"></span><span class="logo-name">HARBORLINE AUTO GLASS</span></div>
<div class="abs nav-band"></div>
<nav class="abs nav"><a class="current" href="#">Home</a><a href="#">About Us</a><a href="#">Services</a><a href="#">Contact</a></nav>
<div class="abs schedule">
  <svg width="34" height="38" viewBox="0 0 34 38" fill="none" stroke="#2a82bd" stroke-width="1.6"><circle cx="13" cy="10" r="6"/><path d="M2 36v-8c0-5 5-8 11-8s11 3 11 8v8"/><rect x="21" y="4" width="11" height="9" rx="1"/></svg>
  <div><h3>Schedule A Service</h3><p>within 24 hour with one of our certified technicians</p></div>
</div>

<div class="abs welcome">
  <div class="pre">WELCOME TO</div>
  <div class="big">HARBORLINE</div>
  <div class="sub">AUTO GLASS</div>
</div>
<p class="abs hero-text">Lorem ipsum dolor sit amet, consectetur adipiscing elit, sed do eiusmod tempor incididunt ut labore et</p>
<a class="abs btn" style="left:144px;top:478px" href="#">Get Started</a>

<section class="abs services">
  <h2>WE HELP YOU WITH</h2>

  <div class="abs service active" style="left:31px;top:132px;height:247px;padding-top:12px">
    <svg width="68" height="44" viewBox="0 0 68 44" fill="none" stroke="#fff" stroke-width="3"><path d="M10 4h48l8 34q-32 6-64 0z"/><path d="M30 4v5h8V4M20 30l8-10M38 30l8-10"/></svg>
    <h4>WINDSHIELD REPAIR</h4>
    <p>Lorem ipsum dolor sit amet, consectetur adipiscing elit, sed do eiusmod tempor incididunt ut labore et dolore magna aliqua. Quis</p>
  </div>
  <div class="abs service" style="left:332px;top:144px">
    <svg width="74" height="50" viewBox="0 0 74 50" fill="none" stroke="#2a82bd" stroke-width="3"><path d="M4 14q30-16 66-4l-6 36q-26-4-52 0z"/><path d="M46 10l6 12-8 10M16 22l4-6M22 24l4-6"/></svg>
    <h4>WINDSHIELD REPLACMENT</h4>
    <p>Lorem ipsum dolor sit amet, consectetur adipiscing elit, sed do eiusmod tempor incididunt ut labore et dolore magna aliqua. Quis</p>
  </div>
  <div class="abs service" style="left:642px;top:138px">
    <svg width="76" height="56" viewBox="0 0 76 56" fill="none" stroke="#2a82bd" stroke-width="3"><path d="M38 2v12M30 8h16"/><rect x="3" y="16" width="70" height="28" rx="5"/><path d="M10 22h56l-4 14H14z"/><path d="M26 42v8h24v-8M28 32l4-4M36 32l6-6M46 30l2-2"/></svg>
    <h4>REAR WINDSHIELD REPLACMENT</h4>
    <p>Lorem ipsum dolor sit amet, consectetur adipiscing elit, sed do eiusmod tempor incididunt ut labore et dolore magna aliqua. Quis</p>
  </div>

  <div class="abs service" style="left:31px;top:416px">
    <svg width="56" height="52" viewBox="0 0 56 52" fill="none" stroke="#2a82bd" stroke-width="2.5"><path d="M20 2h34v48H2V24z"/><path d="M2 24h20M20 2l14 32"/><circle cx="34" cy="36" r="3"/></svg>
    <h4>SIDE WINDOW REPLACMENT</h4>
    <p>Lorem ipsum dolor sit amet, consectetur adipiscing elit, sed do eiusmod tempor incididunt ut labore et dolore magna aliqua. Quis</p>
  </div>
  <div class="abs service" style="left:332px;top:410px">
    <svg width="58" height="58" viewBox="0 0 58 58" fill="none" stroke="#2a82bd" stroke-width="2.5"><path d="M24 2h32v54H2V24z"/><path d="M8 28l18-20h24v20z"/><path d="M6 38h46M6 46h46M40 32h8"/></svg>
    <h4>CAR WINDOW REPLACMENT</h4>
    <p>Lorem ipsum dolor sit amet, consectetur adipiscing elit, sed do eiusmod tempor incididunt ut labore et dolore magna aliqua. Quis</p>
  </div>
  <div class="abs service" style="left:642px;top:420px">
    <svg width="78" height="46" viewBox="0 0 78 46" fill="none" stroke="#2a82bd" stroke-width="3"><path d="M2 2h64l10 42H2z"/><path d="M4 30h70v14H4z" fill="#2a82bd"/><path d="M35 18V6M30 11l5-5 5 5" stroke-width="2.5"/><path d="M35 32v8M31 36l4 4 4-4" stroke="#fff" stroke-width="2.5"/></svg>
    <h4>POWER WINDOW REPAIR</h4>
    <p>Lorem ipsum dolor sit amet, consectetur adipiscing elit, sed do eiusmod tempor incididunt ut labore et dolore magna aliqua. Quis</p>
  </div>
</section>

<div class="abs about-photo" role="img" aria-label="Technician in orange gloves lifting a glass panel with red suction cups"></div>
<section class="abs about">
  <h2>ABOUT US</h2>
  <p>Lorem ipsum dolor sit amet, consectetur adipiscing elit, sed do eiusmod tempor incididunt ut labore et dolore magna aliqua. Quis ipsum suspendisse ultrices gravida. Risus commodo viverra maecenas accumsan lacus vel facilisis. Lorem ipsum dolor sit amet, consectetur adipiscing elit, sed do eiusmod tempor incididunt ut labore et dolore magna aliqua. Quis ipsum suspendisse ultrices gravida. Risus commodo viverra maecenas accumsan lacus vel facilisis. Quis ipsum suspendisse ultrices gravida. Risus commodo viverra maecenas accumsan lacus vel facilisis.</p>
  <a class="btn" href="#">Get Started</a>
</section>

<footer>
  <div class="abs footer"></div>
  <div class="abs foot-logo"><span class="logo-mark"></span><span class="logo-name">HARBORLINE AUTO GLASS</span></div>
  <p class="abs foot-text">Lorem ipsum dolor sit amet, consectetur adipiscing elit, sed do eiusmod tempor incididunt ut labore et dolore magna aliqua.</p>
  <nav class="abs foot-nav"><a href="#">Home</a><a href="#">About Us</a><a href="#">Services</a><a href="#">Contact</a></nav>
  <div class="abs bar">
    <div class="item" style="left:142px">Follow us : <span class="dot" aria-label="Social link"></span><span class="dot" aria-label="Social link"></span><span class="dot" aria-label="Social link"></span></div>
    <div class="item" style="left:390px"><svg width="10" height="14" viewBox="0 0 10 14"><path d="M5 0a5 5 0 0 1 5 5c0 4-5 9-5 9S0 9 0 5a5 5 0 0 1 5-5z" fill="#fff"/><circle cx="5" cy="5" r="2" fill="#3d4047"/></svg>41 Pier Road, Bayview, 40217</div>
    <div class="item" style="left:726px"><svg width="18" height="13" viewBox="0 0 18 13" fill="none" stroke="#fff" stroke-width="1.4"><rect x="1" y="1" width="16" height="11"/><path d="M1 1l8 6 8-6"/></svg>info@harborline.test</div>
    <div class="item" style="left:930px"><svg width="14" height="14" viewBox="0 0 14 14"><path d="M3 0l3 3-2 2q2 3 5 5l2-2 3 3-2 3Q6 13 0 3z" fill="#fff"/></svg>555-014-2370</div>
  </div>
  <div class="abs copy">© copyrights 2022 Harborline Auto Glass | All Rights Reserved</div>
</footer>

</body>
</html>
```